Card design for orthopaedic surgeons working as The Brightwater Joint Centre

Business cards, letterhead

Colors

Designer to choose colors to be used in the design.

Requirements
Must have
• Late addition.
• Cards letterhead must have logos of
• Crestmoor Lindell College of Surgeons
• Varenwood Bone Health Association
Nice to have
• Back of card to have space for appointment time to be added by hand and some blank space for writing incidental other notes.

```html
<!DOCTYPE html>
<html lang="en">
<head>
<meta charset="UTF-8">
<title>The Brightwater Joint Centre – Business Card</title>
<link rel="stylesheet" href="https://fonts.googleapis.com/css2?family=Arimo:wght@700&family=Open+Sans:wght@400;600&display=swap">
<style>
  :root {
    --sky: #33b1f7;
    --navy: #0f3550;
    --ink: #1b1b1b;
    --paper: #ffffff;
    --rule: #b9c2c9;
    --backdrop-top: #b4b6b8;
    --backdrop-bottom: #e3e5e7;
  }
  * { margin: 0; padding: 0; box-sizing: border-box; }
  html, body { width: 1200px; height: 1200px; overflow: hidden; }
  body {
    background: linear-gradient(180deg, var(--backdrop-top), var(--backdrop-bottom));
    font-family: "Open Sans", sans-serif;
    position: relative;
  }
  .card {
    position: absolute;
    left: 250px;
    width: 700px;
    height: 400px;
    border-radius: 34px;
    overflow: hidden;
    box-shadow: 0 8px 22px rgba(0,0,0,0.22);
  }
  .card-back { top: 150px; background: var(--sky); color: var(--paper); }
  .card-front { top: 640px; background: var(--paper); }

  .card-back .brand-name {
    position: absolute; top: 140px; width: 100%; text-align: center;
    font-size: 42px; font-weight: 400; color: var(--paper); letter-spacing: 0.5px;
  }
  .card-back .web {
    position: absolute; top: 216px; width: 100%; text-align: center;
    font-size: 19px; letter-spacing: 7px;
  }

  .card-front .band { position: absolute; inset: 0; width: 700px; height: 400px; }
  .card-front .brand-name {
    position: absolute; top: 56px; width: 100%; text-align: center;
    font-size: 38px; font-weight: 400; color: var(--navy); letter-spacing: 0.5px;
  }
  .person { position: absolute; top: 150px; left: 60px; width: 270px; text-align: right; }
  .person-name { font-family: "Arimo", sans-serif; font-weight: 700; font-size: 30px; color: var(--navy); }
  .person-title { font-size: 24px; color: var(--sky); margin-top: 4px; }
  .divider { position: absolute; top: 150px; left: 350px; width: 1px; height: 80px; background: var(--rule); }
  .contacts { position: absolute; top: 148px; left: 370px; list-style: none; }
  .contacts li { display: flex; align-items: center; gap: 10px; font-size: 18px; color: var(--ink); height: 28px; }
  .contacts svg { width: 16px; height: 16px; flex: none; }
  .address {
    position: absolute; left: 46px; bottom: 24px; display: flex; align-items: center; gap: 10px;
    color: var(--paper); font-size: 18px;
  }
  .address svg { width: 24px; height: 24px; }
  .affiliations {
    position: absolute; right: 40px; bottom: 20px; display: flex; gap: 12px;
  }
  .affiliation-badge {
    width: 34px; height: 34px; border-radius: 50%; background: var(--paper);
  }
</style>
</head>
<body>
  <section class="card card-back">
    <p class="brand-name">The Brightwater Joint Centre</p>
    <p class="web">www.brightwaterjoint.com</p>
  </section>

  <section class="card card-front">
    <svg class="band" viewBox="0 0 700 400" aria-hidden="true">
      <path d="M0,235 C200,290 430,370 700,330 L700,400 L0,400 Z" fill="var(--sky)"/>
      <path d="M0,210 C170,262 380,332 610,342 C380,324 170,252 0,224 Z" fill="var(--navy)"/>
    </svg>

    <p class="brand-name">The Brightwater Joint Centre</p>

    <div class="person">
      <p class="person-name">Maren Holloway</p>
      <p class="person-title">Title</p>
    </div>
    <div class="divider"></div>
    <ul class="contacts">
      <li>
        <svg viewBox="0 0 16 16"><circle cx="8" cy="8" r="8" fill="var(--sky)"/><path d="M5.5 4.5l1.5 1.5-1 1c.6 1.3 1.7 2.4 3 3l1-1 1.5 1.5-1.2 1.2C7.7 11.4 4.6 8.3 4.3 5.7z" fill="#fff"/></svg>
        015-482-7730
      </li>
      <li>
        <svg viewBox="0 0 16 16"><rect x="1" y="3" width="14" height="10" rx="1.5" fill="var(--sky)"/><path d="M1.5 4l6.5 5 6.5-5" fill="none" stroke="#fff" stroke-width="1.4"/></svg>
        info@brightwaterjoint.com
      </li>
      <li>
        <svg viewBox="0 0 16 16"><circle cx="8" cy="8" r="7" fill="none" stroke="var(--sky)" stroke-width="1.5"/><ellipse cx="8" cy="8" rx="3" ry="7" fill="none" stroke="var(--sky)" stroke-width="1.2"/><path d="M1 8h14" stroke="var(--sky)" stroke-width="1.2"/></svg>
        www.brightwaterjoint.com
      </li>
    </ul>

    <p class="address">
      <svg viewBox="0 0 24 24"><circle cx="12" cy="12" r="12" fill="#fff"/><path d="M12 5a4.5 4.5 0 0 0-4.5 4.5c0 3.4 4.5 8.5 4.5 8.5s4.5-5.1 4.5-8.5A4.5 4.5 0 0 0 12 5z" fill="var(--sky)"/><circle cx="12" cy="9.5" r="1.7" fill="#fff"/></svg>
      Street Name, City Name, Zipcode - 012345
    </p>

    <div class="affiliations">
      <div class="affiliation-badge" role="img" aria-label="Crestmoor Lindell College of Surgeons membership badge"></div>
      <div class="affiliation-badge" role="img" aria-label="Varenwood Bone Health Association membership badge"></div>
    </div>
  </section>
</body>
</html>
```